Book Cover with this title and sub title
Where Auntie Found Her Quiet Orchard
The little book to be smart with your money and help the environment.
Walter P. Brunk Ph. D.
Ellen R. Brunk
Picture below would be on the entire front cover. Words somehow incorporated for easy reading.

```html
<!DOCTYPE html>
<html lang="en">
<head>
<meta charset="utf-8">
<title>Where Auntie Found Her Quiet Orchard</title>
<link rel="stylesheet" href="https://fonts.googleapis.com/css2?family=Bebas+Neue&family=Cinzel:wght@400&display=swap">
<style>
  :root {
    --ink: #ffffff;
    --shade: rgba(0, 0, 0, 0.55);
    --bloom: #f4c20d;
    --bloom-deep: #e6a400;
    --leaf: #3d4a2a;
    --soil: #2a2418;
    --night: #15140e;
  }
  html, body {
    margin: 0;
    padding: 0;
    overflow: hidden;
    background: var(--night);
  }
  .cover {
    position: relative;
    width: 934px;
    height: 1200px;
    overflow: hidden;
    color: var(--ink);
    text-align: center;
  }
  .cover-photo {
    position: absolute;
    inset: 0;
    background:
      radial-gradient(ellipse 38% 30% at 42% 60%, rgba(90, 70, 30, 0.55), rgba(90, 70, 30, 0) 70%),
      radial-gradient(ellipse 75% 55% at 55% 68%, var(--bloom) 0%, var(--bloom-deep) 45%, rgba(200, 150, 20, 0.6) 65%, rgba(0, 0, 0, 0) 85%),
      radial-gradient(ellipse 40% 30% at 5% 55%, rgba(61, 74, 42, 0.9), rgba(61, 74, 42, 0) 80%),
      linear-gradient(180deg, var(--night) 0%, var(--soil) 30%, var(--leaf) 60%, var(--soil) 100%);
  }
  .title, .subtitle, .authors {
    position: absolute;
    left: 0;
    right: 0;
    margin: 0;
    text-shadow: 0 3px 10px var(--shade);
  }
  .title-lead {
    position: absolute;
    left: 0; right: 0;
    top: 104px;
    font-family: "Bebas Neue", sans-serif;
    font-size: 76px;
    line-height: 1;
    letter-spacing: 1px;
  }
  .title-link {
    position: absolute;
    left: 0; right: 0;
    top: 205px;
    font-family: "Cinzel", serif;
    font-size: 31px;
    letter-spacing: 9px;
    line-height: 1;
  }
  .title-main {
    position: absolute;
    left: 0; right: 0;
    top: 258px;
    font-family: "Bebas Neue", sans-serif;
    font-size: 158px;
    line-height: 1;
    letter-spacing: 2px;
  }
  .subtitle {
    top: 436px;
    padding: 0 150px;
    font-family: "Bebas Neue", sans-serif;
    font-size: 47px;
    line-height: 54px;
  }
  .authors {
    top: 1040px;
    font-family: "Bebas Neue", sans-serif;
    font-size: 58px;
    line-height: 64px;
    letter-spacing: 13px;
  }
  .author { display: block; }
</style>
</head>
<body>
  <main class="cover">
    <div class="cover-photo" role="img" aria-label="Close-up photograph of a honeybee gathering pollen on a bright yellow dandelion, dark foliage behind"></div>
    <h1 class="title">
      <span class="title-lead">Where Auntie Found</span>
      <span class="title-link">HER QUIET</span>
      <span class="title-main">ORCHARD</span>
    </h1>
    <p class="subtitle">The little book to be smart with your money and help the environment.</p>
    <p class="authors">
      <span class="author">WALTER P. BRUNK PH. D.</span>
      <span class="author">ELLEN R. BRUNK</span>
    </p>
  </main>
</body>
</html>
```